Membership Based Medical Practice Website

We need a functioning website for a new Membership based medical practice. There will be an enrollment fee and a monthly fee. We would like to see designs that are modern, simple. Should use neutral light colors. Examples of sites we like are www.kellanmoorclinic.com and https://fernholtcare.com/ We also have a link that when "Join Now" is clicked it will go to the signup website.

Target Market(s)

Gay Men, local population, Age group 20 to 60's.

Industry/Entity Type

Medical

Coding

Coded - Design and coding required

Number of Pages Required

5+ page

Font styles to use
Sans Serif

Colors
ffffff
cee9f5
ecf7fb
cfeae6
edf8f6
aaaaaa
e9e9e9
dbdbdb
fff3d1

Requirements
Must have
• Logo and header on every page. Clean, simple design, clear content, mobile compatible.
• Must use Wordpress
Nice to have
• Ideas should come from kellanmoorclinic.com
• Easy to read
Should not have
• Generic patient pictures, bold colors.
• Should not copy from above websites.

```html
<!DOCTYPE html>
<html lang="en">
<head>
<meta charset="utf-8">
<title>Larkvale Infectious Disease Specialists</title>
<link href="https://fonts.googleapis.com/css2?family=Raleway:wght@400;500;600;700&display=swap" rel="stylesheet">
<style>
:root{
  --white:#ffffff;
  --sky:#cee9f5;
  --sky-pale:#ecf7fb;
  --cream:#fff3d1;
  --cream-deep:#f7e3ad;
  --grey-light:#e9e9e9;
  --grey:#aaaaaa;
  --gold:#d4a84b;
  --ink:#1d1d1d;
  --dark:#2b2c2e;
  --icon-blue:#bfe3f4;
}
*{box-sizing:border-box;margin:0;padding:0}
html,body{width:1200px;height:3352px;overflow:hidden}
body{position:relative;background:var(--white);font-family:"Raleway",sans-serif;color:var(--ink)}
.abs{position:absolute}
.center{text-align:center}

.topbar{left:0;top:0;width:1200px;height:40px;background:var(--sky)}
.topbar .social{left:110px;top:14px;display:flex;gap:9px}
.topbar .social span{width:11px;height:11px;border-radius:50%;background:var(--ink);display:block}
.topbar .address{right:110px;top:12px;font-size:12px;display:flex;align-items:center;gap:6px}

.header{left:0;top:40px;width:1200px;height:116px;background:var(--white)}
.contact{top:32px;display:flex;align-items:center;gap:12px;font-size:16px;line-height:1.3}
.contact .label{color:var(--gold)}
.contact.call{left:128px}
.contact.mail{left:827px}
.brand-mark{left:555px;top:12px;width:90px;height:90px;border:2px solid var(--gold);border-radius:50%;display:flex;align-items:center;justify-content:center;color:var(--gold);font-size:13px;font-weight:600;letter-spacing:2px}

.nav{left:0;top:156px;width:1200px;height:61px;background:var(--grey-light)}
.nav a{position:absolute;top:21px;font-size:17px;font-weight:500;color:var(--ink);text-decoration:none}
.nav .nav-brand{left:430px;width:340px;top:10px;text-align:center;color:#555;line-height:1.05}
.nav .nav-brand .n1{font-size:20px;letter-spacing:17px}
.nav .nav-brand .n2{font-size:15px}

.hero{left:0;top:217px;width:1200px;height:793px;background:
  radial-gradient(ellipse 420px 260px at 560px 620px,rgba(244,190,120,.55),rgba(244,190,120,0) 70%),
  linear-gradient(180deg,#5a5857 0%,#6f6762 40%,#8a7662 70%,#4e443b 100%)}
.hero-mark{left:513px;top:345px;width:174px;height:174px;border:3px solid var(--white);border-radius:50%}
.hero-brand{left:0;top:558px;width:1200px;color:var(--white);text-align:center;line-height:1.12}
.hero-brand .n1{font-size:34px;letter-spacing:36px;font-weight:400;padding-left:36px}
.hero-brand .n2{font-size:31px;font-weight:400}

.lead-title{top:1033px;left:0;width:1200px;font-size:27px;font-weight:600;color:var(--gold)}
.lead-sub{top:1080px;left:0;width:1200px;font-size:16px}
.expertise{top:1127px;left:0;width:1200px;font-size:20px;font-weight:700}
.card{top:1178px;width:320px;height:208px}
.card .photo{height:170px;width:100%}
.card .label{height:38px;background:var(--sky);font-size:21px;font-weight:500;display:flex;align-items:center;justify-content:center}
.arrow-btn{width:36px;height:36px;border:2px solid var(--ink);border-radius:50%;display:flex;align-items:center;justify-content:center}

.feature-band{left:0;top:1453px;width:1200px;height:720px}
.intro{top:1584px;left:0;width:1200px;color:var(--white);font-size:21px;line-height:1.6}
.feature{top:1690px;width:340px;color:var(--white);text-align:center}
.feature h3{margin-top:24px;font-size:21px;font-weight:700}
.feature p{margin-top:12px;font-size:14px;line-height:1.85}

.pricing-photo{left:90px;top:2253px;width:434px;height:434px;border-radius:50%;background:radial-gradient(circle at 45% 50%,#e6e6e6 0%,#9a8f8f 30%,#7b1f24 60%,#3a1214 100%)}
.pricing-ring{left:86px;top:2240px;width:450px;height:450px;border-radius:50%;border:6px solid var(--gold);clip-path:inset(0 0 0 30%)}
.pricing h2{position:absolute;left:579px;top:2290px;font-size:33px;font-weight:600;color:var(--gold)}
.pricing .plan{position:absolute;left:579px;top:2345px;font-size:16px;font-weight:600}
.pricing ul{position:absolute;left:579px;top:2385px;list-style:none}
.pricing li{display:flex;align-items:center;gap:12px;height:38.7px;font-size:15px;color:#555}
.pricing .btn{position:absolute;left:579px;top:2582px;width:203px;height:49px;background:var(--sky);font-size:16px;font-weight:600;display:flex;align-items:center;justify-content:center;color:var(--ink)}

.footer{left:0;top:2738px;width:1200px;height:614px}
.foot-item{top:3013px;width:320px;text-align:center;color:var(--white);font-size:18px;line-height:1.6}
.foot-icon{width:84px;height:84px;border-radius:50%;background:var(--icon-blue);margin:0 auto 18px;display:flex;align-items:center;justify-content:center}
.foot-links{top:3200px;left:0;width:1200px;color:var(--white);font-size:15px;font-weight:600}
.copyright{top:3242px;left:0;width:1200px;color:var(--white);font-size:14px}
.foot-social{top:3282px;left:530px;display:flex;gap:6px}
.foot-social span{width:31px;height:31px;border:2px solid var(--white);border-radius:50%;display:block}
</style>
</head>
<body>

<div class="abs topbar">
  <div class="abs social" aria-label="Social links"><span></span><span></span><span></span><span></span><span></span><span></span><span></span></div>
  <div class="abs address">
    <svg width="10" height="14" viewBox="0 0 10 14"><path d="M5 0a5 5 0 0 0-5 5c0 4 5 9 5 9s5-5 5-9a5 5 0 0 0-5-5zm0 7a2 2 0 1 1 0-4 2 2 0 0 1 0 4z" fill="#1d1d1d"/></svg>
    48 Orchard Bend Lane, Alder, Texas 75010
  </div>
</div>

<header class="abs header">
  <div class="abs contact call">
    <svg width="44" height="44" viewBox="0 0 44 44"><circle cx="22" cy="22" r="20" fill="none" stroke="#d4a84b" stroke-width="3"/><path d="M15 12c2 0 3 4 3 5s-2 2-2 3c1 3 4 6 7 7 1 0 2-2 3-2s5 1 5 3-2 4-4 4c-8 0-16-8-16-16 0-2 2-4 4-4z" fill="#d4a84b"/></svg>
    <div><div class="label">Call us</div><div>(555) 214-7730</div></div>
  </div>
  <div class="abs brand-mark">LARKVALE</div>
  <div class="abs contact mail">
    <svg width="54" height="36" viewBox="0 0 54 36"><rect x="2" y="2" width="50" height="32" fill="#d4a84b"/><path d="M2 2l25 18L52 2" fill="none" stroke="#fff" stroke-width="3"/></svg>
    <div><div class="label">Email us</div><div>info@larkvaleid.com</div></div>
  </div>
</header>

<nav class="abs nav">
  <a style="left:105px">HOME</a>
  <a style="left:194px">SPECIALTIES</a>
  <a style="left:331px">PRICING</a>
  <a class="nav-brand"><div class="n1">LARKVALE</div><div class="n2">INFECTIOUS DISEASE SPECIALISTS</div></a>
  <a style="left:793px">ABOUT</a>
  <a style="left:890px">FAQ</a>
  <a style="left:961px">BLOG</a>
  <a style="left:1044px">JOIN US</a>
</nav>

<div class="abs hero" role="img" aria-label="Photo of four friends with arms around each other watching a sunset"></div>
<div class="abs hero-mark"></div>
<div class="abs hero-brand"><div class="n1">LARKVALE</div><div class="n2">INFECTIOUS DISEASE SPECIALISTS</div></div>
<svg class="abs" style="left:0;top:780px" width="1200" height="232" viewBox="0 0 1200 232">
  <path d="M0 78C300 38 520 4 820 22S1120 120 1200 140V232H0Z" fill="var(--white)"/>
  <path d="M0 86C300 46 530 16 830 34S1120 140 1200 165V232H0Z" fill="var(--cream)"/>
  <path d="M0 90C300 52 560 34 860 58S1130 180 1200 218V232H0Z" fill="var(--white)"/>
</svg>

<div class="abs lead-title center">SPECIALTY MEDICINE WITH COMMITMENT, COMPASSION AND CARE</div>
<div class="abs lead-sub center">We offer comprehensive treatment of a wide variety of infectious diseases.</div>
<div class="abs expertise center">OUR EXPERTISE IS IN THE FOLLOWING AREA.</div>

<div class="abs arrow-btn" style="left:31px;top:1265px"><svg width="12" height="14" viewBox="0 0 12 14"><path d="M9 1L3 7l6 6" fill="none" stroke="#1d1d1d" stroke-width="2.5"/></svg></div>
<div class="abs card" style="left:89px"><div class="photo" role="img" aria-label="Illustration of virus particles among red blood cells" style="background:radial-gradient(circle at 60% 50%,#c2185b,#6a1b4d 55%,#2a0f2e)"></div><div class="label">HIV/PREP</div></div>
<div class="abs card" style="left:440px"><div class="photo" role="img" aria-label="Illustration of orange hepatitis virus particles" style="background:radial-gradient(circle at 50% 50%,#f28c28,#c8502a 50%,#7ba1b8)"></div><div class="label">Chronic Hepatitis</div></div>
<div class="abs card" style="left:789px"><div class="photo" role="img" aria-label="Illustration of glowing knee joints in blue" style="background:radial-gradient(circle at 55% 50%,#c05ad0,#2f6fd0 45%,#0d2a6b)"></div><div class="label">Bone and Joint infections</div></div>
<div class="abs arrow-btn" style="left:1131px;top:1265px"><svg width="12" height="14" viewBox="0 0 12 14"><path d="M3 1l6 6-6 6" fill="none" stroke="#1d1d1d" stroke-width="2.5"/></svg></div>

<svg class="abs feature-band" viewBox="0 0 1200 720" role="img" aria-label="Dark photo of a misty road through hills">
  <defs><linearGradient id="bandFill" x1="0" y1="0" x2="0" y2="1"><stop offset="0" stop-color="#3a3b3d"/><stop offset="0.6" stop-color="#2b2c2e"/><stop offset="1" stop-color="#1c1d1e"/></linearGradient></defs>
  <path d="M0 10C300 -10 500 40 800 50S1100 20 1200 10V720H0Z" fill="var(--sky)"/>
  <path d="M0 30C300 10 520 70 820 80S1100 50 1200 45V660C950 620 700 640 400 665S100 690 0 690Z" fill="url(#bandFill)"/>
  <path d="M0 690C100 690 300 660 600 645S1000 660 1200 690" fill="none" stroke="var(--cream)" stroke-width="8"/>
</svg>
<div class="abs intro center">Less wait, more personal.<br>We are not your traditional doctor's office.</div>
<div class="abs arrow-btn" style="left:31px;top:1798px;border-color:#fff"><svg width="12" height="14" viewBox="0 0 12 14"><path d="M9 1L3 7l6 6" fill="none" stroke="#fff" stroke-width="2.5"/></svg></div>
<div class="abs arrow-btn" style="left:1131px;top:1798px;border-color:#fff"><svg width="12" height="14" viewBox="0 0 12 14"><path d="M3 1l6 6-6 6" fill="none" stroke="#fff" stroke-width="2.5"/></svg></div>

<div class="abs feature" style="left:89px">
  <svg width="170" height="170" viewBox="0 0 170 170"><rect x="35" y="35" width="100" height="100" fill="#fff" transform="rotate(45 85 85)"/><circle cx="85" cy="85" r="58" fill="var(--icon-blue)" stroke="#fff" stroke-width="4"/><circle cx="85" cy="85" r="30" fill="none" stroke="#1d1d1d" stroke-width="5"/><path d="M72 98L98 72" stroke="#1d1d1d" stroke-width="5"/><circle cx="74" cy="74" r="5" fill="#1d1d1d"/><circle cx="96" cy="96" r="5" fill="#1d1d1d"/></svg>
  <h3>STRAIGHTFORWARD PRICING</h3>
  <p>We charge all our patients the same low rate<br>- no surprises.</p>
</div>
<div class="abs feature" style="left:430px">
  <svg width="170" height="170" viewBox="0 0 170 170"><rect x="35" y="35" width="100" height="100" fill="#fff" transform="rotate(45 85 85)"/><circle cx="85" cy="85" r="58" fill="var(--icon-blue)" stroke="#fff" stroke-width="4"/><rect x="58" y="62" width="46" height="44" rx="4" fill="none" stroke="#1d1d1d" stroke-width="5"/><path d="M58 76h46M68 56v10M94 56v10" stroke="#1d1d1d" stroke-width="5"/><circle cx="104" cy="104" r="14" fill="var(--icon-blue)" stroke="#1d1d1d" stroke-width="5"/><path d="M104 96v8h6" fill="none" stroke="#1d1d1d" stroke-width="4"/></svg>
  <h3>AVAILABLE WHEN YOU ARE</h3>
  <p>New patient appointments are available<br>within 1 week.</p>
</div>
<div class="abs feature" style="left:760px">
  <svg width="170" height="170" viewBox="0 0 170 170"><rect x="35" y="35" width="100" height="100" fill="#fff" transform="rotate(45 85 85)"/><circle cx="85" cy="85" r="58" fill="var(--icon-blue)" stroke="#fff" stroke-width="4"/><rect x="60" y="62" width="50" height="46" rx="4" fill="none" stroke="#1d1d1d" stroke-width="5"/><path d="M60 76h50M70 56v10M100 56v10" stroke="#1d1d1d" stroke-width="5"/><path d="M72 92l8 8 16-16" fill="none" stroke="#1d1d1d" stroke-width="5"/></svg>
  <h3>HASSLE-FREE BOOKING</h3>
  <p>Schedule your appointment online at your<br>convenience - no need to call during<br>business hours.</p>
</div>

<div class="abs pricing-ring"></div>
<div class="abs pricing-photo" role="img" aria-label="Photo of a hand holding a white enamel camping mug"></div>
<section class="pricing">
  <h2>OUR PRICING</h2>
  <div class="plan">Membership Plan $80/mo, plus a one-time $99 enrollment fee.</div>
  <ul>
    <li><svg width="14" height="14" viewBox="0 0 14 14"><circle cx="7" cy="7" r="7" fill="#555"/><path d="M4 7l2 2 4-4" fill="none" stroke="#fff" stroke-width="1.8"/></svg>Includes all appointments, no co-pay</li>
    <li><svg width="14" height="14" viewBox="0 0 14 14"><circle cx="7" cy="7" r="7" fill="#555"/><path d="M4 7l2 2 4-4" fill="none" stroke="#fff" stroke-width="1.8"/></svg>Relaxed, unrushed visits</li>
    <li><svg width="14" height="14" viewBox="0 0 14 14"><circle cx="7" cy="7" r="7" fill="#555"/><path d="M4 7l2 2 4-4" fill="none" stroke="#fff" stroke-width="1.8"/></svg>Direct communication with your doctor via phone, email, video chat 24/7</li>
    <li><svg width="14" height="14" viewBox="0 0 14 14"><circle cx="7" cy="7" r="7" fill="#555"/><path d="M4 7l2 2 4-4" fill="none" stroke="#fff" stroke-width="1.8"/></svg>Convenient online scheduling (no need to call during business hours)</li>
    <li><svg width="14" height="14" viewBox="0 0 14 14"><circle cx="7" cy="7" r="7" fill="#555"/><path d="M4 7l2 2 4-4" fill="none" stroke="#fff" stroke-width="1.8"/></svg>Wholesale price for labs and medications</li>
  </ul>
  <a class="btn">Learn more about us</a>
</section>

<svg class="abs footer" viewBox="0 0 1200 614" role="img" aria-label="Dark photo of a misty road at dusk">
  <path d="M0 0C150 90 400 120 700 100S1100 60 1200 40V614H0Z" fill="var(--sky)"/>
  <path d="M0 40C200 110 450 140 750 120S1100 90 1200 80V614H0Z" fill="var(--white)"/>
  <path d="M0 70C200 130 450 160 750 140S1100 110 1200 100V614H0Z" fill="var(--sky)"/>
  <path d="M0 95C200 150 450 175 750 160S1100 135 1200 125V614H0Z" fill="#2a2b2d"/>
</svg>

<div class="abs foot-item" style="left:124px">
  <div class="foot-icon"><svg width="34" height="40" viewBox="0 0 34 40"><path d="M17 2a12 12 0 0 0-12 12c0 9 12 22 12 22s12-13 12-22A12 12 0 0 0 17 2z" fill="none" stroke="#1d1d1d" stroke-width="2.5"/><circle cx="17" cy="14" r="4.5" fill="none" stroke="#1d1d1d" stroke-width="2.5"/></svg></div>
  1907 Willow Crest Road,<br>Avonport, ND - 58120
</div>
<div class="abs foot-item" style="left:428px">
  <div class="foot-icon"><svg width="36" height="36" viewBox="0 0 44 44"><path d="M12 6c3 0 5 6 5 7s-3 3-3 4c2 5 6 9 11 11 1 0 3-3 4-3s7 2 7 5-3 6-6 6C18 36 6 24 6 12c0-3 3-6 6-6z" fill="none" stroke="#1d1d1d" stroke-width="2.5"/></svg></div>
  Phone:<br>555-214 7730
</div>
<div class="abs foot-item" style="left:732px">
  <div class="foot-icon"><svg width="40" height="30" viewBox="0 0 40 30"><rect x="2" y="2" width="36" height="26" fill="none" stroke="#1d1d1d" stroke-width="2.5"/><path d="M2 2l18 14L38 2M2 28l13-12M38 28L25 16" fill="none" stroke="#1d1d1d" stroke-width="2.5"/></svg></div>
  Email:<br>info@larkvaleid.com
</div>
<div class="abs foot-links center">Home &nbsp;|&nbsp; Specialties &nbsp;|&nbsp; Pricing &nbsp;|&nbsp; About Us &nbsp;|&nbsp; Faq &nbsp;|&nbsp; Blog &nbsp;|&nbsp; Join Us</div>
<div class="abs copyright center">© 2019 Company Name &nbsp;All right reserved</div>
<div class="abs foot-social" aria-label="Social links"><span></span><span></span><span></span><span></span></div>

</body>
</html>
```